A new presentation to our clients

we are a Real Estate agency, our website is www.lumibrasa.com and it’s time to have a new, fashion and remarcable Business Card. we want to differentiate ourselves from other companies so we want a business card that differentiates us. we want the business card to impact our customers. in the competitive market that we have today, we have to be different and it is this difference that we seek

Target Market(s)

Real Estate Clients

Contact Information for Business Card

We search a totaly diferent card from the usual

Font styles to use
Sans Serif

Colors
e34197

Requirements
Must have
• Logo, adress, phone contact, e-mail, photo, and our website
Nice to have
• We would like to see a modern business card
Should not have
• Houses or building draws

```html
<!DOCTYPE html>
<html lang="en">
<head>
<meta charset="UTF-8">
<title>Lumibrasa Business Card</title>
<link href="https://fonts.googleapis.com/css2?family=Lato:wght@400;700&display=swap" rel="stylesheet">
<style>
  :root {
    --stage: #1e1e20;
    --card: #464952;
    --pink: #e8317a;
    --ink: #f2f2f4;
  }
  * { margin: 0; padding: 0; box-sizing: border-box; }
  html, body { width: 1200px; height: 1200px; overflow: hidden; }
  body {
    background: radial-gradient(ellipse at center, #2a2a2d 0%, var(--stage) 75%);
    font-family: "Lato", sans-serif;
    position: relative;
  }
  .card {
    position: absolute;
    left: 140px;
    width: 920px;
    height: 525px;
    background: var(--card);
    border-radius: 32px;
    box-shadow: 0 18px 40px rgba(0,0,0,.55);
  }
  .card--front { top: 48px; }
  .card--back { top: 640px; }
  .wordmark {
    position: absolute;
    color: var(--pink);
    font-weight: 700;
    font-size: 104px;
    line-height: 1;
    letter-spacing: -1px;
    white-space: nowrap;
  }
  .card--front .wordmark { left: 58px; top: 70px; }
  .card--back .wordmark { right: 60px; top: 358px; }
  .person {
    position: absolute;
    left: 58px;
    top: 278px;
    font-size: 35px;
    color: var(--ink);
    line-height: 1;
  }
  .person .surname { color: var(--pink); }
  .role {
    position: absolute;
    left: 58px;
    top: 320px;
    font-size: 24px;
    color: var(--pink);
    line-height: 1;
  }
  .rule {
    position: absolute;
    left: 218px;
    right: 59px;
    top: 335px;
    height: 2px;
    background: var(--pink);
  }
  .contacts {
    position: absolute;
    left: 58px;
    top: 370px;
    list-style: none;
  }
  .contacts li {
    display: flex;
    align-items: center;
    height: 29px;
    font-size: 20px;
    color: var(--ink);
  }
  .contacts svg { width: 22px; height: 22px; margin-right: 16px; fill: var(--pink); }
  .contacts .accent { color: var(--pink); }
  .address {
    position: absolute;
    right: 59px;
    top: 438px;
    text-align: right;
    font-size: 21px;
    line-height: 23px;
    color: var(--ink);
  }
</style>
</head>
<body>
  <section class="card card--front">
    <div class="wordmark">Lumibrasa</div>
    <div class="person">RAFA <span class="surname">DORIN</span></div>
    <div class="role">CEO/manager</div>
    <div class="rule"></div>
    <ul class="contacts">
      <li><svg viewBox="0 0 24 24"><path d="M7 1h10a2 2 0 0 1 2 2v18a2 2 0 0 1-2 2H7a2 2 0 0 1-2-2V3a2 2 0 0 1 2-2zm0 3v14h10V4zm5 15.5a1.2 1.2 0 1 0 0 2.4 1.2 1.2 0 0 0 0-2.4z"/></svg>+123 - 456 - 9789</li>
      <li><svg viewBox="0 0 24 24"><path d="M2 9c0-3 4-5 10-5s10 2 10 5v2h-5V9H7v2H2zM6 12h12l3 8H3zm6 2a2.5 2.5 0 1 0 0 5 2.5 2.5 0 0 0 0-5z"/></svg>+123 - 456 - 9789</li>
      <li><svg viewBox="0 0 24 24"><path d="M2 5h20v14H2zm2 2v1l8 5 8-5V7l-8 5z"/></svg>hello@lumibrasa.com</li>
      <li><svg viewBox="0 0 24 24"><path d="M12 2a10 10 0 1 0 0 20 10 10 0 0 0 0-20zm-1.5 2.2C9.4 5.6 8.7 7.5 8.5 10.5H4.1a8 8 0 0 1 6.4-6.3zm3 0a8 8 0 0 1 6.4 6.3h-4.4c-.2-3-.9-4.9-2-6.3zM12 4.4c1 1.3 1.8 3.3 2 6.1h-4c.2-2.8 1-4.8 2-6.1zM4.1 12.5h4.4c.2 3 .9 4.9 2 6.3a8 8 0 0 1-6.4-6.3zm5.9 0h4c-.2 2.8-1 4.8-2 6.1-1-1.3-1.8-3.3-2-6.1zm5.5 0h4.4a8 8 0 0 1-6.4 6.3c1.1-1.4 1.8-3.3 2-6.3z"/></svg>www.<span class="accent">lumibrasa</span>.com</li>
    </ul>
    <div class="address">Ferro Lane 4180<br>Vale Street Porto Alto</div>
  </section>
  <section class="card card--back">
    <div class="wordmark">Lumibrasa</div>
  </section>
</body>
</html>
```